Financial Services Consultant needs a business card

We need a business card for a new consulting company based in Melbourne called
"Quelbrook Insights". Tagline is Measure, Monitor, Save
We would like to see business card designs that are in line with the minimal style of the website www.quelbrook-insights.example
The font I have used on the website is Proxima Nova and would like the same or similar font used on the business card with a minimal design in line with the website Two sided with "QUELBROOK INSIGHTS" MEASURE, MONITOR, SAVE on one side and name, title and contact details on the otther
Updates

Hi All, thanks for your submissions, much appreciated.

I have recently added some colour to my webiste, it is hex #3a7b74 for those that wish to use it
Thanks

Hi all

thanks very much for your design submissions I am very impressed and they are much appreciated.

Interms of general feedback please find below;

Colour: I am trying to stick to a minimal design and colour scheme for my website which is still under construction, up to 3 colours( www.quelbrook-insights.example) it is currently black and white with a small amount of blue/green but I am open to suggestion/interpretations for a consulting company.

Card: I dont mind if it has rounded edges or straight, I was thinking about using a letterpress card if possible

Detail: the detail on the card will include; Name, Title, Mobile, Personal Email, Business Email,Web,Business Address

Once again thanks for submissions

Industry/Entity Type

Business

```html
<!DOCTYPE html>
<html lang="en">
<head>
<meta charset="utf-8">
<title>Quelbrook Insights – Business Card (Contact Side)</title>
<link rel="stylesheet" href="https://fonts.googleapis.com/css2?family=Montserrat:wght@300;400;700&display=swap">
<style>
  :root {
    --page-bg: #ffffff;
    --card-teal: #3d7b73;
    --card-shadow: #9a9a9a;
    --ink-light: #ffffff;
  }
  html, body {
    margin: 0;
    padding: 0;
    width: 1000px;
    height: 1200px;
    overflow: hidden;
    background: var(--page-bg);
  }
  .canvas {
    position: relative;
    width: 1000px;
    height: 1200px;
    font-family: "Montserrat", "Helvetica Neue", Arial, sans-serif;
    color: var(--ink-light);
  }
  .card-shadow {
    position: absolute;
    left: 209px;
    top: 92px;
    width: 606px;
    height: 1052px;
    background: var(--card-shadow);
    filter: blur(3px);
  }
  .card {
    position: absolute;
    left: 201px;
    top: 76px;
    width: 600px;
    height: 1050px;
    background: var(--card-teal);
  }
  .line {
    position: absolute;
    left: 0;
    width: 1000px;
    text-align: center;
    white-space: nowrap;
    line-height: 1;
  }
  .name {
    top: 220px;
    font-weight: 700;
    font-size: 40px;
  }
  .title {
    top: 286px;
    font-weight: 400;
    font-size: 41px;
  }
  .brace {
    position: absolute;
    top: 214px;
    width: 50px;
    height: 142px;
  }
  .brace--left { left: 226px; }
  .brace--right { left: 722px; }
  .address {
    font-weight: 300;
    font-size: 35px;
  }
  .address--street { top: 402px; }
  .address--city { top: 452px; }
  .contact {
    font-weight: 300;
    font-size: 35px;
  }
  .contact strong {
    font-weight: 700;
    margin-right: 8px;
  }
  .contact--phone { top: 548px; }
  .contact--fax { top: 594px; }
  .contact--email { top: 644px; font-size: 33px; }
  .website {
    top: 996px;
    font-weight: 700;
    font-size: 30px;
  }
</style>
</head>
<body>
  <main class="canvas">
    <div class="card-shadow"></div>
    <section class="card" aria-label="Business card, contact side"></section>

    <svg class="brace brace--left" viewBox="0 0 50 142" aria-hidden="true">
      <path d="M44 2 C22 2 20 10 20 26 L20 56 C20 66 14 70 4 71 C14 72 20 76 20 86 L20 116 C20 132 22 140 44 140"
            fill="none" stroke="#ffffff" stroke-width="11"/>
    </svg>
    <svg class="brace brace--right" viewBox="0 0 50 142" aria-hidden="true">
      <path d="M6 2 C28 2 30 10 30 26 L30 56 C30 66 36 70 46 71 C36 72 30 76 30 86 L30 116 C30 132 28 140 6 140"
            fill="none" stroke="#ffffff" stroke-width="11"/>
    </svg>

    <div class="line name">John Doe</div>
    <div class="line title">Marketing Manager</div>

    <div class="line address address--street">123 Somewhere Lane</div>
    <div class="line address address--city">City, State, 12345</div>

    <div class="line contact contact--phone"><strong>Phone:</strong> 555·555·5555</div>
    <div class="line contact contact--fax"><strong>Fax:</strong> 555·555·5555</div>
    <div class="line contact contact--email"><strong>E-mail:</strong>yourname@qlbmail.com</div>

    <div class="line website">www.quelbrook-insights.example</div>
  </main>
</body>
</html>
```